Elegant Business Card for Technology Company

Client is a supplier of innovative industrial communications and automation equipment since 2002. This contest is to gather fresh ideas for a redesign of the existing business card. Client is looking for design that best communicates tagline "Industrial Networking and Computing Specialist".

Design submissions should look modern, clean, elegant and professional. It should not be cluttered. Use white as the primary colour. Orange and black as secondary colour. Refer to jpeg File 1 on the current design.

Fonts used by Client used include Arial Regular, Arial Black, Roboto Regular, Roboto Black and Lato.

The winning design will be sent for offset printing using super white 250gsm artcard paper (open for suggestions).

Target Market(s)

System Engineers, Project Managers, Purchasing Managers from companies providing engineering services for Smart Cities.

Industry/Entity Type

Information Technology

Contact Information for Business Card

Refer to PDF File 3 for Business Card Details. Priority of short contact information would be as follows Name > Job Title > Email > Mobile > Web > Tel > Fax > Business Address >UEN (UEN represents company registration number)

Font styles to use
Sans Serif

Colors
ffffff
f37122
000000
5c5c5c

Requirements
Must have
• Refer to AI File 2 (Company Logo) & PDF File 3 (Information on Namecard)
Should not have
• No QR codes
• No Social Media Icons
• Do not create full Black or Orange colour background

```html
<!DOCTYPE html>
<html lang="en">
<head>
<meta charset="utf-8">
<title>Korvex Business Card</title>
<link href="https://fonts.googleapis.com/css2?family=Lato:wght@400;700;900&display=swap" rel="stylesheet">
<style>
  :root {
    --white: #ffffff;
    --orange: #f37122;
    --black: #000000;
    --ink: #1c1c1c;
    --grey: #5c5c5c;
    --stage: #2b2b2b;
  }
  * { margin: 0; padding: 0; box-sizing: border-box; }
  html, body {
    width: 1200px; height: 1166px; overflow: hidden;
    background: var(--stage);
    font-family: 'Lato', sans-serif;
  }
  .card {
    position: absolute; left: 170px;
    width: 860px; height: 491px;
    background: var(--white);
    overflow: hidden;
    box-shadow: 0 10px 30px rgba(0,0,0,.45);
  }
  .card--front { top: 60px; }
  .card--back { top: 615px; }

  .brand {
    position: absolute;
    display: flex; align-items: center; gap: 14px;
  }
  .brand__dot {
    width: 46px; height: 46px; border-radius: 50%;
    background: var(--orange);
  }
  .brand__name {
    font-weight: 900; color: var(--black);
    letter-spacing: 2px; line-height: 1;
  }
  .card--front .brand { left: 90px; top: 200px; }
  .card--front .brand__name { font-size: 58px; }

  .divider {
    position: absolute; left: 470px; top: 150px;
    width: 1.5px; height: 150px; background: var(--ink);
  }
  .services {
    position: absolute; left: 492px; top: 160px;
    list-style: none; color: var(--ink); font-size: 18px; line-height: 26px;
  }
  .services li::before {
    content: ""; display: inline-block;
    width: 6px; height: 6px; border-radius: 50%;
    background: var(--orange); margin: 0 8px 3px 0;
  }
  .tagline {
    position: absolute; right: 56px; bottom: 52px;
    font-size: 21px; color: var(--ink); letter-spacing: .3px;
  }

  .card--back .brand { left: 520px; top: 62px; }
  .card--back .brand__name { font-size: 52px; }
  .person { position: absolute; left: 560px; top: 160px; }
  .person__name { font-size: 32px; color: var(--ink); font-weight: 400; }
  .person__title { font-size: 22px; color: var(--orange); }

  .contact {
    position: absolute; left: 60px; top: 210px;
    color: var(--ink); font-size: 21px; line-height: 27px;
  }
  .contact__company { color: var(--orange); }
  .contact__lines { list-style: none; margin-top: 10px; }
  .contact__lines li { display: flex; align-items: center; gap: 12px; }
  .contact__lines svg { width: 18px; height: 18px; fill: var(--orange); }
  .contact__uen { margin-top: 10px; font-size: 22px; }

  .swoosh { position: absolute; inset: 0; width: 860px; height: 491px; }
  .web {
    position: absolute; right: 40px; bottom: 40px;
    color: var(--white); font-size: 20px; letter-spacing: 1px;
  }
</style>
</head>
<body>

<section class="card card--front">
  <div class="brand"><span class="brand__dot"></span><span class="brand__name">KORVEX</span></div>
  <div class="divider"></div>
  <ul class="services">
    <li>Industrial Ethernet / Wireless / Cellular</li>
    <li>Industrial and Embedded Computing</li>
    <li>Serial / Fieldbus Connectivity</li>
    <li>IP Video Surveillance</li>
    <li>Remote Automation</li>
  </ul>
  <p class="tagline">Industrial Networking and Computing Specialist</p>
</section>

<section class="card card--back">
  <svg class="swoosh" viewBox="0 0 860 491" aria-hidden="true">
    <path d="M250 491 C540 440 760 360 860 240 L860 275 C770 380 560 450 330 491 Z" fill="var(--orange)"/>
    <path d="M360 491 C600 450 790 380 860 295 L860 491 Z" fill="var(--black)"/>
  </svg>

  <div class="brand"><span class="brand__dot"></span><span class="brand__name">KORVEX</span></div>
  <div class="person">
    <p class="person__name">Daniel Lim</p>
    <p class="person__title">Sales manager</p>
  </div>

  <div class="contact">
    <p class="contact__company">Korvex Asia Pacific Pte Ltd</p>
    <p>22 Harbour Link</p>
    <p>Harbour Techpark #05-12 (Lobby B)</p>
    <p>Singapore 409001</p>
    <ul class="contact__lines">
      <li><svg viewBox="0 0 24 24"><path d="M6.6 10.8a15 15 0 0 0 6.6 6.6l2.2-2.2c.3-.3.7-.4 1-.2 1.1.4 2.3.6 3.6.6.6 0 1 .4 1 1V20c0 .6-.4 1-1 1A17 17 0 0 1 3 4c0-.6.4-1 1-1h3.5c.6 0 1 .4 1 1 0 1.3.2 2.5.6 3.6.1.3 0 .7-.2 1z"/></svg>+65 6100 2040</li>
      <li><svg viewBox="0 0 24 24"><path d="M7 1h10a2 2 0 0 1 2 2v18a2 2 0 0 1-2 2H7a2 2 0 0 1-2-2V3a2 2 0 0 1 2-2zm0 3v14h10V4zm5 15.5a1 1 0 1 0 0 2 1 1 0 0 0 0-2z"/></svg>+65 9100 3050</li>
      <li><svg viewBox="0 0 24 24"><path d="M6 2h12v5H6zM4 8h16a2 2 0 0 1 2 2v7h-4v5H6v-5H2v-7a2 2 0 0 1 2-2zm4 8v4h8v-4z"/></svg>+65 6100 2041</li>
      <li><svg viewBox="0 0 24 24"><path d="M2 5h20v14H2zm2 2v.5l8 5 8-5V7zm0 2.8V17h16V9.8l-8 5z"/></svg>sales@korvex.com.sg</li>
    </ul>
    <p class="contact__uen">UEN No 200301145K</p>
  </div>

  <p class="web">www.korvex.com.sg</p>
</section>

</body>
</html>
```